SaaS Early tech startup business card design

Unique design for experience ecommerce platform company. the business cards will be used by executive members. conformance with color code is required.

```html
<!DOCTYPE html>
<html lang="en">
<head>
<meta charset="utf-8">
<title>Velto Business Card</title>
<link rel="stylesheet" href="https://fonts.googleapis.com/css2?family=Montserrat:wght@500;700&display=swap">
<style>
  :root {
    --bg: #e9eaee;
    --navy: #23233b;
    --navy-deep: #1c1c31;
    --teal: #2cc4a6;
    --teal-blue: #1d7fa0;
    --white: #ffffff;
  }
  html, body {
    margin: 0;
    width: 1200px;
    height: 900px;
    overflow: hidden;
    background: var(--bg);
    font-family: "Montserrat", Arial, sans-serif;
  }
  .canvas { position: relative; width: 1200px; height: 900px; }
  .card {
    position: absolute;
    width: 640px;
    height: 366px;
    border-radius: 22px;
    background: var(--navy);
    overflow: hidden;
    box-shadow: 0 10px 30px rgba(20, 20, 40, 0.25);
  }
  .card-front { left: 80px; top: 50px; }
  .card-back { left: 480px; top: 474px; }

  .brand-name {
    font-weight: 700;
    color: var(--teal);
    letter-spacing: 1px;
    line-height: 1;
  }
  .card-front .brand-name {
    position: absolute;
    left: 0; right: 0; top: 128px;
    text-align: center;
    font-size: 110px;
  }
  .card-back .brand-name {
    position: absolute;
    right: 40px; top: 26px;
    font-size: 70px;
  }

  .wave { position: absolute; inset: 0; }

  .person {
    position: absolute;
    left: 34px; top: 58px;
    border-left: 5px solid var(--teal);
    padding-left: 12px;
  }
  .person-name { color: var(--teal); font-weight: 700; font-size: 26px; letter-spacing: 0.5px; }
  .person-role { color: var(--white); font-weight: 500; font-size: 17px; margin-top: 2px; }

  .contact-list {
    position: absolute;
    left: 40px; top: 160px;
    list-style: none; margin: 0; padding: 0;
  }
  .contact-item {
    display: flex; align-items: center; gap: 10px;
    color: var(--white); font-size: 19px; font-weight: 500;
    height: 29px;
  }
  .contact-icon {
    width: 22px; height: 22px; border-radius: 5px;
    background: var(--teal);
    display: flex; align-items: center; justify-content: center;
  }

  .address {
    position: absolute;
    right: 34px; top: 240px;
    text-align: right;
    color: var(--white); font-size: 18px; font-weight: 500; line-height: 1.3;
  }
</style>
</head>
<body>
<main class="canvas">

  <section class="card card-front" aria-label="Card front">
    <div class="brand-name">Velto</div>
  </section>

  <section class="card card-back" aria-label="Card back">
    <svg class="wave" width="640" height="366" viewBox="0 0 640 366">
      <defs>
        <linearGradient id="band" x1="0" y1="0" x2="1" y2="0">
          <stop offset="0" stop-color="var(--teal-blue)"/>
          <stop offset="0.45" stop-color="#2294a8"/>
          <stop offset="0.6" stop-color="#3ab89f"/>
          <stop offset="1" stop-color="var(--teal)"/>
        </linearGradient>
      </defs>
      <path d="M0,344 C240,336 370,314 450,254 C520,200 575,170 640,160 L640,366 L0,366 Z" fill="url(#band)"/>
      <path d="M0,332 C240,324 365,302 445,242 C515,188 572,158 640,148 L640,160 C575,170 520,200 450,254 C370,314 240,336 0,344 Z" fill="var(--navy-deep)"/>
      <path d="M0,320 C240,312 360,290 440,230 C510,176 570,146 640,136" fill="none" stroke="var(--white)" stroke-width="9"/>
      <path d="M180,304 C290,292 370,266 432,220" fill="none" stroke="var(--white)" stroke-width="3" stroke-linecap="round"/>
    </svg>

    <div class="brand-name">Velto</div>

    <div class="person">
      <div class="person-name">Daniel Carter</div>
      <div class="person-role">Manager</div>
    </div>

    <ul class="contact-list">
      <li class="contact-item">
        <span class="contact-icon">
          <svg width="14" height="14" viewBox="0 0 14 14"><path d="M3 1.5 L5.2 1.5 L6 4.2 L4.6 5.3 C5.3 7 6.9 8.6 8.6 9.4 L9.8 8 L12.5 8.8 L12.5 11 C12.5 12 11.7 12.5 10.8 12.4 C6 11.8 2.2 8 1.6 3.2 C1.5 2.3 2 1.5 3 1.5 Z" fill="var(--white)"/></svg>
        </span>555-014-2738
      </li>
      <li class="contact-item">
        <span class="contact-icon">
          <svg width="14" height="14" viewBox="0 0 14 14"><rect x="1.5" y="3" width="11" height="8" fill="none" stroke="var(--white)" stroke-width="1.4"/><path d="M1.5 3 L7 7.5 L12.5 3" fill="none" stroke="var(--white)" stroke-width="1.4"/></svg>
        </span>youremail@mailhub.com
      </li>
      <li class="contact-item">
        <span class="contact-icon">
          <svg width="14" height="14" viewBox="0 0 14 14"><circle cx="7" cy="7" r="5.3" fill="none" stroke="var(--white)" stroke-width="1.4"/><ellipse cx="7" cy="7" rx="2.3" ry="5.3" fill="none" stroke="var(--white)" stroke-width="1.2"/><line x1="1.7" y1="7" x2="12.3" y2="7" stroke="var(--white)" stroke-width="1.2"/></svg>
        </span>www.yourwebsite.com
      </li>
    </ul>

    <div class="address">Your address, city<br>state, ZIP 0000</div>
  </section>

</main>
</body>
</html>
```